I need a complete stationary pack for a real estate office that sells and manages residential proper

We need a stationary design pack for my real estate office called ‘brightkeyhomes’ that is in Queensland Australia. My offices are both in suburban and coastal locations in the south west corner of Queensland at the Coral Bay Shore and Brisbane.
We predominately manage real estate on behalf of owners and sell property in the residential sector.
I have attached a copy of our existing design of my business card and do like the current concept/layout. In saying this you may be able to use this existing theme across to the other items required or see opportunity on how to improve what I have already.
I would like to see concepts for the following products:
- Letterhead
- Fax header
- Business cards
- Email signature
- With complements slips and
- Envelopes
I have attached our current logo that was designed by Artfolder and the font is Prelo.

I am looking for a contemporary design that is professional and reflects trust and professionalism. I am currently using the logo with a black background on some material as per the following link

http://www.plotlisting.com.au/property/for-sale/house/qld/merridale/?adid=4827305118&sp=7

I have posted another job 517362 for signage and the company car signage done too if you are interested.

Please do not hesitate to contact me should you have any questions. Thank you.

Target Market(s)

Western speaking people aged from 25 to 60 from modest backgrounds to well off individuals

Industry/Entity Type

Real Estate

Requirements
Must have
• Professional in appearance, show a mature and trustworthy image
Should not have
• As there is good colour with the logo, i am do not want over the top designs or colours

```html
<!DOCTYPE html>
<html lang="en">
<head>
<meta charset="utf-8">
<title>brightkeyhomes business card</title>
<link rel="stylesheet" href="https://fonts.googleapis.com/css2?family=Open+Sans:wght@400;600;700&display=swap">
<style>
  :root {
    --page: #ecebe8;
    --card-dark: #111111;
    --card-light: #ffffff;
    --ink: #2e3a4a;
    --ink-soft: #5a5f66;
    --white: #ffffff;
    --green: #2aa63f;
    --red: #d8232f;
    --orange: #f07c1e;
    --blue: #1f8ad6;
    --photo-top: #6b8fb8;
    --photo-bottom: #3d4a5c;
  }
  * { margin: 0; padding: 0; box-sizing: border-box; }
  html, body {
    width: 1200px; height: 1024px; overflow: hidden;
    background: var(--page);
    font-family: "Open Sans", Arial, sans-serif;
  }
  .sheet {
    position: relative; width: 1200px; height: 1024px;
    display: flex; flex-direction: column; align-items: center; justify-content: center; gap: 56px;
  }
  .card {
    width: 700px; height: 420px; position: relative; overflow: hidden;
    box-shadow: 0 10px 28px rgba(0,0,0,0.18);
  }
  /* front */
  .card-front { background: var(--card-dark); color: var(--white); }
  .front-brand {
    position: absolute; left: 0; right: 0; top: 150px;
    display: flex; flex-direction: column; align-items: center; gap: 18px;
  }
  .front-brand .brand-mark {
    display: flex; align-items: center; gap: 16px;
  }
  .brand-dot {
    width: 46px; height: 46px; border-radius: 50%; background: var(--green);
  }
  .front-brand .brand-name {
    font-size: 50px; font-weight: 600; letter-spacing: -1px; color: var(--white);
  }
  .front-url { font-size: 18px; letter-spacing: 0.3px; color: var(--white); }
  .front-url .url-domain { color: var(--green); }

  /* back */
  .card-back { background: var(--card-light); color: var(--ink); }
  .back-brand {
    position: absolute; left: 52px; top: 52px;
    display: flex; align-items: center; gap: 14px;
  }
  .back-brand .brand-dot { width: 36px; height: 36px; }
  .back-brand .brand-name {
    font-size: 38px; font-weight: 600; letter-spacing: -0.8px; color: var(--ink);
  }
  .divider {
    position: absolute; left: 52px; right: 52px; top: 168px;
    height: 2px; background: var(--green);
  }
  .contact {
    position: absolute; left: 52px; top: 196px;
    font-size: 16px; line-height: 1.42; color: var(--ink-soft);
  }
  .contact .person-name { font-size: 21px; font-weight: 700; color: var(--red); line-height: 1.25; }
  .contact .person-role { font-size: 17px; color: var(--green); margin-bottom: 4px; }
  .contact .label { font-weight: 600; }
  .label-mobile { color: var(--orange); }
  .label-phone, .label-email { color: var(--red); }
  .contact .web-domain { color: var(--blue); }
  .portrait {
    position: absolute; right: 52px; top: 196px;
    width: 150px; height: 124px;
    background: linear-gradient(180deg, var(--photo-top), var(--photo-bottom));
  }
</style>
</head>
<body>
  <main class="sheet">
    <section class="card card-front" aria-label="Business card front">
      <div class="front-brand">
        <div class="brand-mark">
          <span class="brand-dot"></span>
          <span class="brand-name">brightkeyhomes</span>
        </div>
        <p class="front-url">www.<span class="url-domain">brightkeyhomes</span>.com.au</p>
      </div>
    </section>

    <section class="card card-back" aria-label="Business card back">
      <div class="back-brand">
        <span class="brand-dot"></span>
        <span class="brand-name">brightkeyhomes</span>
      </div>
      <div class="divider"></div>
      <div class="contact">
        <p class="person-name">Marcus Delane</p>
        <p class="person-role">Principal</p>
        <p>shop 4, 212 harbour parade,</p>
        <p>merridale qld 4571</p>
        <p><span class="label label-mobile">M:</span> 0412305867</p>
        <p><span class="label label-phone">P:</span> 07 5521 6048</p>
        <p><span class="label label-email">E:</span> marcus@brightkeyhomes.com.au</p>
        <p>www.<span class="web-domain">brightkeyhomes</span>.com.au</p>
      </div>
      <div class="portrait" role="img" aria-label="Portrait photo of the agent"></div>
    </section>
  </main>
</body>
</html>
```